Maranoola Wines - web page for new Australian wine label

We need a landing page for our wine company. Maranoola is a family owned company, we grow the gapes, and make the wine in the Clare valley. Daniel Whitlock is the winemaker and is well known for his style, which is all about the fruit flavour rather than wood or age influences. Maranoola is Abriginal for 2 hills and a water source. We hand pick, hand plunge, foot crush resulting in elegant wine. Little to no additives, minimal filtering, single vineyard wines. Handcrafted with small releases of only the best fruit from carefully selected rows and bunches. The Clare valley is located two hours North of Adelaide, is known for cool climate and slow ripening, resulting in wines that have an elegant mouth feel, with bright colour and outstanding flavours. Our Brookmere vineyard has a Eastern aspect, gathering morning sun and escaping the hot afternoons, and in our opinion is on of the prettiest valleys in the world. Only 1000 cases per annum of the very best handpicked fruit, from the best rows. We hope you enjoy the Maranoola style, the reds are lighter in colour, fruit driven palate, more old world influence and the Riesling is on the dry side with fresh citrus. Minimal additives and filtering, our aim was to make wine with minimal influence from wine making. Handcrafted wines.

Target Market(s)

females 18 - 60 are the ones that buy 70 percent of wine, so whilst men are also a target, its the ladies we seek to appeal to.

Industry/Entity Type

It Company

Number of Pages Required

4 page

Font styles to use
Serif

Requirements
Must have
• Eye catching front page that makes me feel like i am ordering from quality company, that cares for what they do. Easy to use ordering, and delivery instructions.
• postage is $14.90 per case Australia wide.
• www.maranoolawines-example.com
Nice to have
• I want to see a fun and family oriented business that cares for the wine, we dont make a lot, its buckets and feet. But its wine made wanting to be the best in the world, we dont cut corners on quality. Handcrafted
Should not have
• dont really have any thoughts here, looking for all ideas

```html
<!DOCTYPE html>
<html lang="en">
<head>
<meta charset="utf-8">
<title>Maranoola Wines</title>
<link href="https://fonts.googleapis.com/css2?family=Lora:wght@400;600;700&family=Roboto:wght@400;500;700&display=swap" rel="stylesheet">
<style>
:root{
  --blue:#1a5aa8;
  --navy:#123e93;
  --grey-band:#e6e6e6;
  --ink:#333;
  --white:#fff;
  --field-line:#aab4d8;
}
*{margin:0;padding:0;box-sizing:border-box}
html,body{width:1200px;height:2899px;overflow:hidden;background:var(--white)}
body{position:relative;font-family:"Lora",Georgia,serif;color:var(--ink)}
h1,h2{font-weight:400}
.abs{position:absolute}
.center{left:0;width:1200px;text-align:center}

/* hero */
.hero{top:0;left:0;width:1200px;height:645px}
.menu-icon{left:1070px;top:40px;width:32px}
.menu-icon span{display:block;height:5px;background:var(--white);margin-bottom:6px;border-radius:1px}
.brand-hero{top:130px;font-family:"Lora",serif;font-size:72px;font-weight:400;color:var(--white)}
.hero-title{top:270px;font-family:"Roboto",sans-serif;font-size:58px;font-weight:700;color:var(--white)}
.btn-outline{border:2px solid var(--white);color:var(--white);font-family:"Roboto",sans-serif;display:flex;align-items:center;justify-content:center}
.hero-btn{left:446px;top:386px;width:306px;height:64px;font-size:27px}
.slider-dots{left:553px;top:594px;display:flex;gap:12px}
.slider-dots span{width:13px;height:13px;background:var(--white)}
.slider-dots span.active{background:#3a3ab8}

/* welcome */
.section-title{font-family:"Roboto",sans-serif;color:var(--blue)}
.welcome-title{top:708px;font-size:37px;font-weight:500}
.welcome-text{left:268px;top:784px;width:664px;font-size:12px;line-height:21px;text-align:justify;text-align-last:center;color:#555}

/* special band */
.special{top:931px;left:0;width:1200px;height:379px}
.special-title{top:992px;font-family:"Roboto",sans-serif;font-size:34px;font-weight:400;color:var(--white)}
.special-text{left:212px;top:1068px;width:776px;font-size:12px;line-height:20.5px;color:var(--white);text-align:justify;text-align-last:center}
.special-btn{left:527px;top:1205px;width:145px;height:35px;font-family:"Lora",serif;font-weight:700;font-size:16px;border-width:1.5px}

/* blog */
.blog{top:1310px;left:0;width:1196px;height:634px;background:var(--grey-band)}
.blog-title{top:1346px;font-size:35px;font-weight:500}
.blog-card{top:1424px;width:277px;height:479px;background:var(--white);box-shadow:0 1px 4px rgba(0,0,0,.25)}
.blog-photo{position:absolute;left:0;top:0;width:277px;height:193px}
.blog-date{position:absolute;left:0;top:145px;width:79px;height:83px;background:var(--blue);color:var(--white);font-family:"Roboto",sans-serif;font-size:29px;line-height:33px;padding:8px 0 0 13px}
.blog-text{position:absolute;left:26px;top:258px;width:225px;font-size:11px;line-height:20px;text-align:justify;text-align-last:center;color:#444}
.btn-blue{position:absolute;top:415px;left:85px;width:107px;height:33px;background:var(--blue);color:var(--white);font-family:"Lora",serif;font-size:16px;display:flex;align-items:center;justify-content:center}

/* testimonials */
.testi-title{top:1982px;font-size:44px;font-weight:400}
.testi-box{top:2083px;width:439px;height:162px;border:1px solid #888;padding:36px 30px 0;font-size:11px;line-height:20.5px;text-align:center;color:#444}
.avatar{width:70px;height:70px;border-radius:50%;background:linear-gradient(#9aa3ad,#5d6670);border:3px solid #3d5d85}
.testi-name{font-size:13px;font-weight:700;color:#111}

/* footer */
.footer{top:2376px;left:0;width:1200px;height:523px;background:var(--navy)}
.footer-title{top:2420px;font-family:"Roboto",sans-serif;font-size:34px;font-weight:400;color:var(--white)}
.contact-row{left:226px;display:flex;align-items:center;color:var(--white);font-size:15px}
.contact-row svg{width:22px;height:22px;margin-right:22px;fill:var(--white)}
.field{left:672px;width:320px;border-bottom:1px solid var(--field-line);color:var(--white);font-size:12px;padding-bottom:1px;text-decoration:underline}
.send-btn{left:894px;top:2774px;width:98px;height:34px;font-size:19px;border-width:1.5px}
.brand-footer{left:155px;top:2738px;font-family:"Lora",serif;font-size:62px;color:var(--white)}
.copyright{top:2855px;font-size:13px;color:var(--white)}
</style>
</head>
<body>

<svg class="abs hero" viewBox="0 0 1200 645" role="img" aria-label="Wine bottle and glass of red wine beside lily of the valley flowers">
  <defs>
    <linearGradient id="heroFill" x1="0" y1="0" x2="1" y2="0">
      <stop offset="0" stop-color="#4d4741"/>
      <stop offset=".5" stop-color="#6a5f55"/>
      <stop offset="1" stop-color="#2a2420"/>
    </linearGradient>
  </defs>
  <path d="M0 0H1200V575Q600 690 0 575Z" fill="url(#heroFill)"/>
</svg>
<div class="abs menu-icon"><span></span><span></span><span></span></div>
<div class="abs center brand-hero">Maranoola</div>
<h1 class="abs center hero-title">PASSION OF QUALITY</h1>
<div class="abs btn-outline hero-btn">Contact Us Today</div>
<div class="abs slider-dots"><span class="active"></span><span></span><span></span><span></span></div>

<h2 class="abs center section-title welcome-title">Welcome To Maranoola</h2>
<p class="abs welcome-text">The enchanting Maranoola Vineyard is situated on the north-eastern ridge of the valley, and consists mainly of clay loam soil. This Reserve Shiraz is hand harvested, 50% whole bunch ferment, in open top fermenters. The balance being de-stemmed. Gentle foot crushing and hand plunging was used during ferment. After 6 weeks the wine was basket pressed directly to 2-5 year old barriques. After elevage of 1 year the wine was bottled under gravity without fining or filtration. 65 Dozen produced. Drink 2017-2025.</p>

<div class="abs special" role="img" aria-label="Dark vineyard foliage with grape bunches" style="background:linear-gradient(160deg,#2c3527,#1c2419 55%,#30392b)"></div>
<h2 class="abs center special-title">What Special In Us</h2>
<p class="abs special-text">We are a small family winery in the Clare Valley. We grow the grapes, pick by hand, crush by foot and plunge by hand, so every bottle carries the pure fruit of our Brookmere vineyard. Its eastern aspect gathers the gentle morning sun and escapes the hot afternoons, giving slow ripening, bright colour and an elegant mouth feel. We use little to no additives and minimal filtering, and release only 1000 cases a year from the best rows and bunches. Ordering is simple: choose your wines, pick the number of cases and send your order below. Postage is $14.90 per case Australia wide.</p>
<div class="abs btn-outline special-btn">Read More</div>

<div class="abs blog"></div>
<h2 class="abs center section-title blog-title">Our Blog</h2>

<article class="abs blog-card" style="left:147px">
  <div class="blog-photo" role="img" aria-label="Hands pressing crushed grapes" style="background:linear-gradient(135deg,#5c5070,#2e2638)"></div>
  <div class="blog-date">02<br>Jan</div>
  <p class="blog-text">Harvest has begun at Brookmere. Family and friends joined us in the rows to hand pick only the best bunches, with buckets full by morning tea and the first ferments started by lunch.</p>
  <div class="btn-blue">Read More</div>
</article>

<article class="abs blog-card" style="left:444px">
  <div class="blog-photo" role="img" aria-label="Family crushing grapes in the winery shed" style="background:linear-gradient(135deg,#7a6a5a,#3e3a35)"></div>
  <div class="blog-date">12<br>Feb</div>
  <p class="blog-text">Buckets and feet: the kids took their turn foot crushing this year's Shiraz. It is gentle, it is messy, and it keeps the fruit bright and pure, just the way Daniel likes it.</p>
  <div class="btn-blue">Read More</div>
</article>

<article class="abs blog-card" style="left:742px">
  <div class="blog-photo" role="img" aria-label="Winemakers working at a steel tank" style="background:linear-gradient(135deg,#a8a69c,#5a5850)"></div>
  <div class="blog-date">25<br>Feb</div>
  <p class="blog-text">Our dry Riesling is now in bottle, with fresh citrus and minimal filtering. Order by the case online; postage is $14.90 per case anywhere in Australia.</p>
  <div class="btn-blue" style="top:410px">Read More</div>
</article>

<h2 class="abs center section-title testi-title">Testimonials</h2>
<blockquote class="abs testi-box" style="left:141px">" The Shiraz is light, bright and full of fruit. You can taste the care in every bottle, and our case arrived at the door in perfect order within a few days. It is now our family's favourite for long Sunday lunches."</blockquote>
<blockquote class="abs testi-box" style="left:617px">" Ordering was so easy and the dry Riesling is beautiful, fresh citrus and so elegant. Knowing it is hand picked and foot crushed by a family makes every glass feel special. We have already ordered our second case."</blockquote>
<div class="abs avatar" style="left:208px;top:2266px" role="img" aria-label="Customer portrait"></div>
<div class="abs testi-name" style="left:294px;top:2291px">-Sarah M., Adelaide customer</div>
<div class="abs avatar" style="left:676px;top:2266px" role="img" aria-label="Customer portrait"></div>
<div class="abs testi-name" style="left:766px;top:2291px">-Emma R., Melbourne customer</div>

<footer class="abs footer"></footer>
<h2 class="abs center footer-title">Get&nbsp; In Touch</h2>

<div class="abs contact-row" style="top:2535px">
  <svg viewBox="0 0 24 24"><path d="M12 3 1 12h3v9h6v-6h4v6h6v-9h3z"/></svg>Maranoola South St, Brookmere Australia
</div>
<div class="abs contact-row" style="top:2576px">
  <svg viewBox="0 0 24 24"><rect x="2" y="2" width="20" height="20" rx="3"/><path d="M8 6c1 0 2 2 2 3s-1 1-1 2 3 4 4 4 1-1 2-1 3 1 3 2-1 2-3 2C10 18 6 14 6 8c0-1 1-2 2-2z" fill="#123e93"/></svg>+61 5550 2841
</div>
<div class="abs contact-row" style="top:2618px">
  <svg viewBox="0 0 24 24"><rect x="2" y="8" width="20" height="13" rx="2"/><rect x="6" y="2" width="12" height="7" fill="none" stroke="#fff" stroke-width="2"/><rect x="6" y="12" width="12" height="2" fill="#123e93"/><rect x="6" y="16" width="12" height="2" fill="#123e93"/></svg>+61 5550 7316
</div>
<div class="abs contact-row" style="top:2659px">
  <svg viewBox="0 0 24 24"><rect x="2" y="5" width="20" height="14" rx="2"/><path d="M2 6l10 7 10-7" fill="none" stroke="#123e93" stroke-width="2"/></svg>info@maranoolawines-example.com
</div>

<div class="abs field" style="top:2522px">Name</div>
<div class="abs field" style="top:2574px">Email</div>
<div class="abs field" style="top:2626px">Number</div>
<div class="abs field" style="top:2678px">Quantity<svg style="position:absolute;right:0;top:3px" width="10" height="8" viewBox="0 0 10 8"><path d="M1 2l4 4 4-4" fill="none" stroke="#fff" stroke-width="1.5"/></svg></div>
<div class="abs field" style="top:2730px">Message*</div>
<div class="abs btn-outline send-btn">Send</div>

<div class="abs brand-footer">Maranoola</div>
<p class="abs center copyright">© 2017&nbsp; Maranoola&nbsp; All right reserved&nbsp; Term of Use</p>

</body>
</html>
```